TolVex BIM business website

I have a logo design and business card concept is ongoing at this point, but i need a website design based on VDC or BIM ("Virtual Building and Construction" or "Building Information Modeling") that will stand out for the quality and concept that we provide. I am a consultant providing training and production work for Planvo (Quorvane application <where most of the overview can be obtained>). We are providing BIM production and coordination services as well. I can fill in the meat but I need an open development website. Currently, just obtaining a domain so it can be included on a business card is the quickest objective, then developing the content and launching it.

```html
<!DOCTYPE html>
<html lang="en">
<head>
<meta charset="utf-8">
<title>TolVex BIM Consulting</title>
<link href="https://fonts.googleapis.com/css2?family=Open+Sans:wght@400;600;700&display=swap" rel="stylesheet">
<style>
:root{
  --navy:#1e2a5a;
  --gold:#e7a23a;
  --grey-bg:#f3f3f3;
  --text:#6f6f6f;
  --footer:#444444;
  --white:#ffffff;
}
*{margin:0;padding:0;box-sizing:border-box}
html,body{width:717px;height:1200px;overflow:hidden;background:var(--white);font-family:"Open Sans",Arial,sans-serif}
.page{position:relative;width:717px;height:1200px}
.header{position:absolute;left:0;top:0;width:717px;height:86px;background:var(--navy)}
.brand{position:absolute;left:78px;top:26px;display:flex;align-items:center;gap:6px;color:var(--gold);font-weight:700;font-size:17px;letter-spacing:.5px}
.brand-dot{width:14px;height:14px;border-radius:50%;background:var(--gold)}
.brand-sub{position:absolute;left:78px;top:52px;color:var(--white);font-size:6px;letter-spacing:2px;font-weight:600}
.login{position:absolute;left:595px;top:19px;width:43px;height:21px;background:var(--gold);color:var(--navy);font-size:7px;font-weight:600;display:flex;align-items:center;justify-content:center;border-radius:2px}
.nav{position:absolute;top:60px;left:341px;display:flex;gap:19px;font-size:7.5px;color:var(--white)}
.nav .active{color:var(--gold)}
.hero{position:absolute;left:0;top:86px;width:717px;height:281px;background:linear-gradient(90deg,#e9e9e6 0%,#2e3f66 35%,#34496f 62%,#9fd8dc 100%)}
.hero-arrow{position:absolute;top:219px}
.welcome-title{position:absolute;top:410px;width:717px;text-align:center;color:var(--navy);font-size:14px;font-weight:700;letter-spacing:.3px}
.welcome-text{position:absolute;left:79px;top:436px;width:559px;text-align:center;color:var(--text);font-size:6.5px;line-height:12.8px}
.row{position:absolute;left:79px;width:559px;height:134px;display:flex}
.row .photo,.row .copy{width:279.5px;height:100%}
.copy{background:var(--grey-bg);padding:0 20px;display:flex;flex-direction:column;justify-content:center}
.copy h3{color:var(--navy);font-size:10px;font-weight:600;line-height:12.5px;margin-bottom:9px}
.copy p{color:var(--text);font-size:6.5px;line-height:11.5px;margin-bottom:9px}
.more{color:var(--gold);font-size:7.5px;font-weight:600;display:flex;align-items:center;gap:3px}
.projects-title{position:absolute;top:966px;width:717px;text-align:center;color:var(--navy);font-size:14px;font-weight:700}
.tiles{position:absolute;left:79px;top:999px;display:flex;gap:1.3px}
.tile{width:138.5px;height:95px}
.slide-btn{position:absolute;top:1040px;width:14px;height:14px;border:1px solid #bdbdbd;display:flex;align-items:center;justify-content:center}
.footer{position:absolute;left:0;top:1142px;width:717px;height:58px;background:var(--footer)}
.footer-links{position:absolute;left:79px;top:17px;font-size:6.5px;color:#e5e5e5}
.footer-links span{margin:0 4px}
.copyright{position:absolute;left:79px;top:32px;font-size:6.5px;color:#d6d6d6}
.social{position:absolute;left:563px;top:22px;display:flex;gap:5px}
.social i{width:14px;height:14px;border-radius:50%;display:block}
</style>
</head>
<body>
<div class="page">
  <header class="header">
    <div class="brand"><span class="brand-dot"></span>TolVex</div>
    <div class="brand-sub">BIM CONSULTING</div>
    <div class="login">LOGIN</div>
    <nav class="nav">
      <span class="active">HOME</span><span>ABOUT US</span><span>SERVICES</span><span>SOLUTIONS</span><span>PROJECTS</span><span>CONTACT US</span>
    </nav>
  </header>

  <section class="hero" role="img" aria-label="Businessman in a suit holding a city skyline in his open hand"></section>
  <svg class="hero-arrow" style="left:14px" width="10" height="16" viewBox="0 0 10 16"><path d="M8 1L2 8l6 7" fill="none" stroke="#8a8a8a" stroke-width="1.6"/></svg>
  <svg class="hero-arrow" style="left:693px" width="10" height="16" viewBox="0 0 10 16"><path d="M2 1l6 7-6 7" fill="none" stroke="#8a8a8a" stroke-width="1.6"/></svg>

  <h1 class="welcome-title">WELCOME TO TOLVEX BIM CONSULTING</h1>
  <p class="welcome-text">Duis iaculis dolor blandit leo dictum, a malesuada ligula cursus. Vivamus vel erat euismod, euismod velit vel, maximus velit. Maecenas tristique justo a gravida facilisis. Quisque a venenatis diam. Pellentesque faucibus, lorem at consectetur congue, tortor purus hendrerit dui, a condimentum justo urna non metus. Maecenas volutpat ultrices massa a tristique. Etiam malesuada ante viverra, vulputate urna eget, rhoncus lectus. Donec ut neque id justo posuere venenatis id et tellus. Curabitur dictum magna ligula, et euismod augue placerat id. Suspendisse porta molestie massa ut sodales. Morbi nibh ipsum, egestas quis lacinia id, varius vel sem.</p>

  <div class="row" style="top:513px">
    <div class="photo" role="img" aria-label="Architectural scale model of glass towers on a table" style="background:linear-gradient(135deg,#8a8f86,#4e6a6a 50%,#b0aa90)"></div>
    <div class="copy">
      <h3>Virtual Building and Construction / Building Information Modelling</h3>
      <p>Quisque ac turpis risus. Proin viverra nulla eu eleifend molestie. Sed sem risus, pharetra vel tristique ornare, placerat quis orci. Donec enim ante, hendrerit non fringilla in, accumsan sit amet lectus.</p>
      <span class="more">MORE <svg width="8" height="8" viewBox="0 0 8 8"><circle cx="4" cy="4" r="3.3" fill="none" stroke="#e7a23a"/><path d="M3.3 2.4L5 4 3.3 5.6" fill="none" stroke="#e7a23a"/></svg></span>
    </div>
  </div>

  <div class="row" style="top:651px">
    <div class="copy">
      <h3>Training and production work for Planvo</h3>
      <p>Quisque ac turpis risus. Proin viverra nulla eu eleifend molestie. Sed sem risus, pharetra vel tristique ornare, placerat quis orci. Donec enim ante, hendrerit non fringilla in, accumsan sit amet lectus.</p>
      <span class="more">MORE <svg width="8" height="8" viewBox="0 0 8 8"><circle cx="4" cy="4" r="3.3" fill="none" stroke="#e7a23a"/><path d="M3.3 2.4L5 4 3.3 5.6" fill="none" stroke="#e7a23a"/></svg></span>
    </div>
    <div class="photo" role="img" aria-label="Hand touching a holographic blue building model on a tablet" style="background:linear-gradient(135deg,#0c1d4e,#1f4f9c 55%,#0b1a44)"></div>
  </div>

  <div class="row" style="top:790px">
    <div class="photo" role="img" aria-label="White 3D city blocks rising from a tablet screen" style="background:linear-gradient(135deg,#e9e9e9,#c7c9cc 60%,#e2e2e2)"></div>
    <div class="copy">
      <h3>BIM production and coordination services</h3>
      <p>Quisque ac turpis risus. Proin viverra nulla eu eleifend molestie. Sed sem risus, pharetra vel tristique ornare, placerat quis orci. Donec enim ante, hendrerit non fringilla in, accumsan sit amet lectus.</p>
      <span class="more">MORE <svg width="8" height="8" viewBox="0 0 8 8"><circle cx="4" cy="4" r="3.3" fill="none" stroke="#e7a23a"/><path d="M3.3 2.4L5 4 3.3 5.6" fill="none" stroke="#e7a23a"/></svg></span>
    </div>
  </div>

  <h2 class="projects-title">PROJECTS</h2>
  <div class="slide-btn" style="left:50px"><svg width="6" height="8" viewBox="0 0 6 8"><path d="M4.5 1L1.5 4l3 3" fill="none" stroke="#9a9a9a"/></svg></div>
  <div class="tiles">
    <div class="tile" role="img" aria-label="Hand sketching a pale blue building concept" style="background:linear-gradient(160deg,#e4ecf0,#9fb8c6)"></div>
    <div class="tile" role="img" aria-label="Glass office building model with plans" style="background:linear-gradient(160deg,#e8e8e8,#9aa0a6)"></div>
    <div class="tile" role="img" aria-label="Exploded 3D building floor model" style="background:linear-gradient(160deg,#303a58,#9aa2b2)"></div>
    <div class="tile" role="img" aria-label="Residential tower rendering over blue blueprints" style="background:linear-gradient(160deg,#0d3fa8,#1f72d8)"></div>
  </div>
  <div class="slide-btn" style="left:653px"><svg width="6" height="8" viewBox="0 0 6 8"><path d="M1.5 1l3 3-3 3" fill="none" stroke="#9a9a9a"/></svg></div>

  <footer class="footer">
    <div class="footer-links">Home<span>|</span>About Us<span>|</span>Services<span>|</span>Solutions<span>|</span>Projects<span>|</span>Contact Us</div>
    <div class="copyright">Copyright © 2017 TolVex Bim Constructions. All rights reserved</div>
    <div class="social" aria-label="Social links">
      <i style="background:#3b5998"></i><i style="background:#1da1f2"></i><i style="background:#0077b5"></i><i style="background:#dd4b39"></i>
    </div>
  </footer>
</div>
</body>
</html>
```